Simple and Clean business card design

We would like the design to be simple clean and to incorporate our colors.

We are open to your design and talent, we have the dots in our logo as we think of it as data points and we connect data points for people.

We are open to see the great creative and clean design you bring to the table

Contact Information for Business Card

please include: name, position, email, phone and website

Font styles to use
Sans Serif

Requirements
Must have
• my colors incorporated, simplicity
Nice to have
• lots of white space, simplicity
Should not have
• complexicity/ complex art

```html
<!DOCTYPE html>
<html lang="en">
<head>
<meta charset="utf-8">
<title>Sorrel Business Card</title>
<link rel="stylesheet" href="https://fonts.googleapis.com/css2?family=Lexend:wght@500&family=Saira:wght@600;700&family=Open+Sans:wght@400;500&display=swap">
<style>
  :root {
    --page-bg: #fdfdfd;
    --ink: #000000;
    --text-dark: #222222;
    --card-white: #ffffff;
    --brand-blue: #4285f4;
    --brand-green: #34a853;
    --brand-yellow: #fbbc05;
    --brand-red: #ea4335;
    --card-border: #3a3a3a;
  }
  * { margin: 0; padding: 0; box-sizing: border-box; }
  html, body {
    width: 1200px; height: 1200px; overflow: hidden;
    background: var(--page-bg);
  }
  .canvas { position: relative; width: 1200px; height: 1200px; }

  .card {
    position: absolute; top: 215px;
    width: 429px; height: 771px;
  }
  .card--back { left: 147px; background: var(--ink); }
  .card--front {
    left: 625px; background: var(--card-white);
    border: 1px solid var(--card-border);
  }

  .wordmark {
    position: absolute;
    display: flex; align-items: center; gap: 10px;
    font-family: "Lexend", sans-serif; font-weight: 500;
    line-height: 1; letter-spacing: -1px;
  }
  .wordmark__dot { border-radius: 50%; flex: none; }

  .card--back .wordmark { left: 78px; top: 610px; font-size: 92px; color: var(--card-white); }
  .card--back .wordmark__dot { width: 22px; height: 22px; background: var(--card-white); }

  .card--front .wordmark { left: 0; right: 0; justify-content: center; top: 240px; font-size: 100px; color: var(--ink); }
  .card--front .wordmark__dot { width: 24px; height: 24px; background: var(--brand-blue); }

  .person { position: absolute; left: 0; right: 0; top: 440px; text-align: center; }
  .person__name {
    font-family: "Saira", sans-serif; font-weight: 700;
    font-size: 38px; letter-spacing: 2px; line-height: 1;
    color: var(--brand-blue);
  }
  .person__role {
    margin-top: 10px;
    display: flex; align-items: center; justify-content: center; gap: 28px;
    font-family: "Saira", sans-serif; font-weight: 600;
    font-size: 20px; letter-spacing: 3px; line-height: 1;
    color: var(--text-dark);
  }
  .person__rule { width: 47px; height: 2px; background: var(--text-dark); }

  .contacts {
    position: absolute; left: 0; right: 0; top: 560px;
    display: flex; flex-direction: column; align-items: center; gap: 12px;
    font-family: "Open Sans", sans-serif; font-size: 20px; font-weight: 500;
    color: var(--text-dark); list-style: none;
  }
  .contacts__item { display: flex; align-items: center; gap: 9px; line-height: 24px; }
  .contacts__icon { width: 22px; height: 22px; flex: none; }

  .divider {
    position: absolute; left: 45px; right: 45px; top: 683px; height: 3px;
    background: linear-gradient(90deg, transparent, #444 50%, transparent);
    border-radius: 2px;
  }
  .address {
    position: absolute; left: 0; right: 0; top: 704px; text-align: center;
    font-family: "Open Sans", sans-serif; font-size: 22px; color: var(--text-dark);
  }
</style>
</head>
<body>
<div class="canvas">
  <section class="card card--back">
    <div class="wordmark"><span>Sorrel</span><span class="wordmark__dot"></span></div>
  </section>

  <section class="card card--front">
    <div class="wordmark"><span>Sorrel</span><span class="wordmark__dot"></span></div>

    <div class="person">
      <div class="person__name">DANIEL REYES</div>
      <div class="person__role"><span class="person__rule"></span>FOUNDER<span class="person__rule"></span></div>
    </div>

    <ul class="contacts">
      <li class="contacts__item">
        <svg class="contacts__icon" viewBox="0 0 24 24" aria-hidden="true">
          <path d="M5 2.5l2.5-1 3 5-2 2c1 2.5 3.5 5.5 6.5 7l2-2 5 3-1 2.5c-.5 1-2 1.5-3 1C10 17.5 5.5 12 3.5 6 3.2 4.8 3.8 3 5 2.5z" fill="var(--brand-blue)"/>
        </svg>
        <span>555-214-0386</span>
      </li>
      <li class="contacts__item">
        <svg class="contacts__icon" viewBox="0 0 24 24" aria-hidden="true" fill="none" stroke="var(--brand-blue)" stroke-width="1.3">
          <circle cx="12" cy="12" r="10.5"/>
          <ellipse cx="12" cy="12" rx="4.5" ry="10.5"/>
          <line x1="12" y1="1.5" x2="12" y2="22.5"/>
          <line x1="1.5" y1="12" x2="22.5" y2="12"/>
          <path d="M3.5 6.5h17M3.5 17.5h17"/>
        </svg>
        <span>www.sorrel.one</span>
      </li>
      <li class="contacts__item">
        <svg class="contacts__icon" viewBox="0 0 26 20" aria-hidden="true" style="width:26px;height:20px">
          <rect x="1" y="2" width="24" height="16" fill="none" stroke="var(--brand-blue)" stroke-width="2"/>
          <path d="M1 2l12 10 12-10M1 18l9-8M25 18l-9-8" fill="none" stroke="var(--brand-blue)" stroke-width="1.6"/>
        </svg>
        <span>daniel.reyes@sorrel.one</span>
      </li>
    </ul>

    <div class="divider"></div>
    <p class="address">Address line goes here</p>
  </section>
</div>
</body>
</html>
```